Valmora Company needs a Business Card Design

We just opened our business recently and we need a business card design. Our basic product are clothes and accessories. We would like to see designs that use bright colors like pink, light blue and purple. In addition to that kindly include also our address in the business card which our main office is located in Los Angeles, California.
The final design should communicate that we have affordable price yet high quality brand.

Target Market(s)

young and middle age women

Industry/Entity Type

Business

Contact Information for Business Card

Valmora Apparel and Accessories 4873 North Bellcrest St. Los Angeles California
Tel: 555-318-6492

Logo Text

Valmora's Apparel and Accessories

Font styles to use
Serif

Requirements
Must have
• there should be a graphic of a sexy lady wearing an elegant dress at the upper left corner of the business card.

```html
<!DOCTYPE html>
<html lang="en">
<head>
<meta charset="utf-8">
<title>Valmora Apparel and Accessories – Business Card</title>
<link rel="stylesheet" href="https://fonts.googleapis.com/css2?family=Arimo:wght@400&family=UnifrakturMaguntia&display=swap">
<style>
  :root {
    --page-bg: #e6e6e8;
    --card-bg: #ffffff;
    --brand-magenta: #b0268f;
    --ink: #111111;
    --photo-light: #f3f3f4;
    --photo-mid: #d9d9db;
    --figure-dark: #141414;
    --figure-accent: #b0268f;
  }
  * { box-sizing: border-box; margin: 0; padding: 0; }
  html, body {
    width: 1200px;
    height: 902px;
    overflow: hidden;
    background: var(--page-bg);
  }
  .business-card {
    position: absolute;
    left: 75px;
    top: 151px;
    width: 1050px;
    height: 600px;
    background: var(--card-bg);
    overflow: hidden;
    box-shadow: 0 6px 24px rgba(0,0,0,0.15);
  }
  .model-photo {
    position: absolute;
    left: 253px;
    top: 0;
    width: 560px;
    height: 600px;
    background: radial-gradient(ellipse at 45% 45%, var(--photo-mid) 0%, var(--photo-light) 55%, rgba(255,255,255,0) 80%);
    opacity: 0.85;
  }
  .lady-figure {
    position: absolute;
    left: 53px;
    top: 40px;
    width: 200px;
    height: 560px;
    background: linear-gradient(180deg, var(--figure-dark) 0%, #2a2a2a 60%, var(--figure-dark) 100%);
    border-radius: 90px 90px 20px 20px;
    border-right: 6px solid var(--figure-accent);
  }
  .brand {
    position: absolute;
    right: 96px;
    top: 62px;
    text-align: right;
    color: var(--brand-magenta);
    font-family: "Arimo", Arial, sans-serif;
    font-weight: 400;
  }
  .brand-name {
    font-size: 64px;
    line-height: 1;
    letter-spacing: 3px;
  }
  .brand-tagline {
    margin-top: 8px;
    font-size: 38px;
    line-height: 1.1;
  }
  .holder {
    position: absolute;
    right: 96px;
    top: 252px;
    text-align: right;
    color: var(--ink);
  }
  .holder-name {
    font-family: "UnifrakturMaguntia", serif;
    font-size: 40px;
    line-height: 1.05;
  }
  .holder-position {
    font-family: "Arimo", Arial, sans-serif;
    font-size: 26px;
    line-height: 1.2;
  }
  .contact-list {
    position: absolute;
    right: 99px;
    top: 440px;
    list-style: none;
    font-family: "Arimo", Arial, sans-serif;
    color: var(--ink);
  }
  .contact-item {
    display: flex;
    justify-content: flex-end;
    align-items: center;
    gap: 14px;
    height: 40px;
    margin-bottom: 8px;
  }
  .contact-phone { font-size: 28px; }
  .contact-address { font-size: 23px; }
  .contact-icon {
    width: 38px;
    height: 38px;
    background: var(--brand-magenta);
    border-radius: 4px;
    display: flex;
    align-items: center;
    justify-content: center;
  }
</style>
</head>
<body>
  <main class="business-card">
    <div class="model-photo" role="img" aria-label="Faded photo of a woman wearing statement necklaces"></div>
    <div class="lady-figure" role="img" aria-label="Silhouette of an elegant lady in a long black dress with pink gloves"></div>

    <header class="brand">
      <div class="brand-name">Valmora</div>
      <div class="brand-tagline">Apparel and Accessories</div>
    </header>

    <section class="holder">
      <div class="holder-name">Your Name</div>
      <div class="holder-position">Position</div>
    </section>

    <ul class="contact-list">
      <li class="contact-item contact-phone">
        <span>555-318-6492</span>
        <span class="contact-icon">
          <svg width="22" height="22" viewBox="0 0 24 24" aria-hidden="true">
            <path fill="#fff" d="M6.6 10.8a15.1 15.1 0 0 0 6.6 6.6l2.2-2.2c.3-.3.7-.4 1-.2 1.1.4 2.3.6 3.6.6.6 0 1 .4 1 1V20c0 .6-.4 1-1 1A17 17 0 0 1 3 4c0-.6.4-1 1-1h3.5c.6 0 1 .4 1 1 0 1.3.2 2.5.6 3.6.1.3 0 .7-.2 1z"/>
          </svg>
        </span>
      </li>
      <li class="contact-item contact-address">
        <span>4873 North Bellcrest St. Los Angeles California</span>
        <span class="contact-icon">
          <svg width="20" height="24" viewBox="0 0 20 24" aria-hidden="true">
            <path fill="#fff" d="M10 1a7 7 0 0 0-7 7c0 5.3 7 14 7 14s7-8.7 7-14a7 7 0 0 0-7-7zm0 9.5A2.5 2.5 0 1 1 10 5.5a2.5 2.5 0 0 1 0 5z"/>
          </svg>
        </span>
      </li>
    </ul>
  </main>
</body>
</html>
```